MRT Property - Business Cards

Looking for a business card & general letterhead, signage etc design for our new logo.

Colours:
000a20
0056a2
00b5ef
0088ce
68cef2

Fonts:
Poppins
Karla

Please keep look and feel of new brand - example in the zip package I sent.

```html
<!DOCTYPE html>
<html lang="en">
<head>
<meta charset="utf-8">
<title>MRT Property – Business Cards</title>
<link rel="stylesheet" href="https://fonts.googleapis.com/css2?family=Poppins:wght@400;600;700&family=Karla:wght@400;500&display=swap">
<style>
  :root {
    --ink: #000a20;
    --brand-blue: #0056a2;
    --card-back: #0d55a3;
    --sky: #00b5ef;
    --mid-blue: #0088ce;
    --pale-blue: #68cef2;
    --paper: #ffffff;
    --stage: #e9ecf1;
    --text: #1c2230;
  }
  * { margin: 0; padding: 0; box-sizing: border-box; }
  html, body { width: 1200px; height: 931px; overflow: hidden; background: var(--stage); }
  .canvas { position: relative; width: 1200px; height: 931px; }

  .card {
    position: absolute; width: 700px; height: 400px; border-radius: 22px; overflow: hidden;
    box-shadow: 0 10px 28px rgba(0, 10, 32, 0.18);
  }
  .card--back { left: 250px; top: 45px; background: var(--card-back); }
  .card--front { left: 250px; top: 486px; background: var(--paper); }

  .wordmark { position: absolute; font-family: "Poppins", sans-serif; font-weight: 700; line-height: 1; }
  .wordmark__dot { display: inline-block; border-radius: 50%; vertical-align: middle; }
  .wordmark__name { display: inline-block; vertical-align: middle; letter-spacing: 2px; }

  .card--back .wordmark { left: 0; right: 0; top: 135px; text-align: center; color: var(--paper); }
  .card--back .wordmark__dot { width: 54px; height: 54px; background: var(--pale-blue); margin-right: 22px; }
  .card--back .wordmark__name { font-size: 110px; }
  .card--back .tagline {
    position: absolute; left: 0; right: 0; top: 262px; text-align: center;
    font-family: "Poppins", sans-serif; font-weight: 600; font-size: 26px; letter-spacing: 14px;
    color: var(--paper); padding-left: 90px;
  }

  .card--front .wordmark { right: 40px; top: 40px; color: var(--brand-blue); }
  .card--front .wordmark__name { font-size: 74px; }
  .card--front .tagline {
    position: absolute; right: 40px; top: 122px;
    font-family: "Poppins", sans-serif; font-weight: 600; font-size: 18px; letter-spacing: 10px;
    color: var(--brand-blue);
  }

  .person { position: absolute; left: 40px; top: 168px; }
  .person__name { font-family: "Karla", sans-serif; font-weight: 500; font-size: 38px; color: var(--ink); }
  .person__role { font-family: "Poppins", sans-serif; font-size: 15px; color: var(--text); margin-top: 2px; }

  .rule { position: absolute; left: 40px; right: 40px; top: 252px; height: 2px; background: var(--brand-blue); }

  .contacts { position: absolute; left: 40px; top: 272px; list-style: none; }
  .contacts li {
    display: flex; align-items: center; gap: 12px; height: 30px;
    font-family: "Poppins", sans-serif; font-size: 16px; color: var(--text);
  }
  .contacts svg { width: 18px; height: 18px; fill: var(--brand-blue); flex: none; }

  .address {
    position: absolute; right: 40px; top: 190px; text-align: right;
    font-family: "Poppins", sans-serif; font-size: 15px; line-height: 1.5; color: var(--text);
  }

  .colour-band { position: absolute; left: 0; right: 0; bottom: 0; height: 16px; display: flex; }
  .colour-band span { flex: 1; }
  .colour-band .b1 { background: var(--pale-blue); }
  .colour-band .b2 { background: var(--sky); }
  .colour-band .b3 { background: var(--mid-blue); }
  .colour-band .b4 { background: var(--brand-blue); }
</style>
</head>
<body>
<div class="canvas">

  <section class="card card--back" aria-label="Card back">
    <div class="wordmark"><span class="wordmark__dot"></span><span class="wordmark__name">MRT</span></div>
    <div class="tagline">PROPERTY</div>
  </section>

  <section class="card card--front" aria-label="Card front">
    <div class="wordmark"><span class="wordmark__name">MRT</span></div>
    <div class="tagline">PROPERTY</div>

    <div class="person">
      <div class="person__name">Daniel Hart</div>
      <div class="person__role">Managing Director</div>
    </div>

    <div class="address">420 Maple Ridge Ave Suite<br>210 Columbus Ohio 43215</div>

    <div class="rule"></div>

    <ul class="contacts">
      <li>
        <svg viewBox="0 0 24 24" aria-hidden="true"><path d="M6.6 10.8a15.1 15.1 0 0 0 6.6 6.6l2.2-2.2a1 1 0 0 1 1-.25 11.4 11.4 0 0 0 3.6.57 1 1 0 0 1 1 1V20a1 1 0 0 1-1 1A17 17 0 0 1 3 4a1 1 0 0 1 1-1h3.5a1 1 0 0 1 1 1c0 1.25.2 2.45.57 3.57a1 1 0 0 1-.25 1z"/></svg>
        1 (530) 555-0148
      </li>
      <li>
        <svg viewBox="0 0 24 24" aria-hidden="true"><path d="M2 5h20v14H2z" opacity=".9"/><path d="M2 5l10 8 10-8" fill="none" stroke="#fff" stroke-width="2"/></svg>
        info@mrtproperty.com
      </li>
      <li>
        <svg viewBox="0 0 24 24" aria-hidden="true"><circle cx="12" cy="12" r="10"/><path d="M2 12h20M12 2c3 3 3 17 0 20M12 2c-3 3-3 17 0 20" fill="none" stroke="#fff" stroke-width="1.5"/></svg>
        www.mrtproperty.com
      </li>
    </ul>

    <div class="colour-band"><span class="b1"></span><span class="b2"></span><span class="b3"></span><span class="b4"></span></div>
  </section>

</div>
</body>
</html>
```